WordPress Website Design & Theme - The Coastal Bidding Firm

Need a WordPress design for an auction company wanting a responsive, simple and easy to use site.

Please keep in mind that the design will be built on a responsive WP theme.

Colors will be light or white and complimentary/highlight colors from the logo.

Industry/Entity Type

It Company

Number of Pages Required

1 page

Font styles to use
Serif
Sans Serif

Requirements
Must have
• Navigation - 1) Home 2) Auction Calendar 3) Auction Results 4) For Sale 5) Services 6)About Us 7) Contact Us
• A site they mention liking is http://www.quillbrookbids.example/
• Site will have full width slideshow 960px. Use stock real estate photo. Header will have logo (attached) and contact info:
• THE COASTAL BIDDING FIRM
• P.O. Box 682
• Gadsden, AL 35917
• PHONE: (800)519-6084 or (256)583-9101
• FAX: (256)583-2260
• EMAIL: info@coastal-bidding.example
• There will be no sidebar on the homepage. There can be 3 horizontal widgets for "featured Listings", Join Our Newsletter, and maybe a form like http://www.coastal-bidding.example/request_proposal.php. The "Upcoming Auctions" feature as is seen on http://www.quillbrookbids.example/ will be used (attached image).
• In the footer: contact info, social media (FB, twitter, RSS), affiliation logos (attached), perhaps smaller company logo, News & Events blog, and if room "Featured Auctions".
Nice to have
• Use of drop-down menus styling- 1) Live Auctions 2) Online Auctions - under the Auction Calendar tab

```html
<!DOCTYPE html>
<html lang="en">
<head>
<meta charset="utf-8">
<title>The Coastal Bidding Firm</title>
<link href="https://fonts.googleapis.com/css2?family=Raleway:wght@400;500;600;700&family=Roboto:wght@300;400;500&display=swap" rel="stylesheet">
<style>
:root{
  --purple:#3a3163;
  --purple-dark:#2c2452;
  --purple-light:#463d74;
  --red:#c8163a;
  --red-dark:#a80f2e;
  --ink:#333;
  --muted:#555;
  --line:#d8d8d8;
  --grey-bg:#f0f0f0;
  --white:#fff;
}
*{box-sizing:border-box;margin:0;padding:0}
html,body{width:1200px;height:2228px;overflow:hidden;background:var(--white)}
body{position:relative;font-family:'Roboto',sans-serif;color:var(--ink);font-size:15px}
.abs{position:absolute}
.topline{left:0;top:0;width:1200px;height:4px;background:#111}
.brand{left:107px;top:40px;display:flex;align-items:center;gap:12px}
.brand-dot{width:58px;height:58px;border-radius:50%;background:var(--red)}
.brand-name{font-family:'Raleway',sans-serif;font-weight:700;font-size:26px;line-height:1.1;color:var(--red);width:170px}
.contact-addr{left:552px;top:60px;font-size:16px;line-height:28px;color:#444;display:flex;gap:12px}
.contact-lines{left:810px;top:60px;font-size:16px;line-height:28px;color:#444}
.contact-lines .row{display:flex;gap:14px;align-items:flex-start}
.contact-lines svg,.contact-addr svg{flex:none;margin-top:6px}
.nav{left:0;top:206px;width:1200px;height:69px;background:linear-gradient(#453b70,#2f2859);border-bottom:3px solid var(--red)}
.nav ul{list-style:none;display:flex;position:absolute;left:107px;top:0;height:66px}
.nav li{font-family:'Raleway',sans-serif;font-size:18px;color:var(--white);padding:0 22px;line-height:66px;border-right:1px solid rgba(255,255,255,.12)}
.nav li.active{background:var(--red);padding:0 32px}
.dropdown{left:217px;top:275px;width:226px;height:122px;background:var(--purple);list-style:none}
.dropdown li{font-family:'Raleway',sans-serif;font-size:15px;color:var(--white);height:50px;line-height:50px;padding-left:18px;border-bottom:1px solid rgba(255,255,255,.12)}
.dropdown li:first-child{margin-top:8px}
.deco{left:0;top:275px;width:1200px;height:470px}
.slider{left:107px;top:296px;width:986px;height:440px;border:1px solid var(--line);padding:4px;background:var(--white)}
.slide{width:100%;height:100%;background:linear-gradient(180deg,#6fa0d6 0%,#a9c6e6 25%,#6b7a78 42%,#2d6e86 60%,#1f6a6a 80%,#3a7f70 100%)}
.slide-title{left:135px;top:335px;font-family:'Raleway',sans-serif;font-weight:700;font-size:28px;color:var(--white)}
.dots{left:563px;top:694px;display:flex;gap:18px}
.dots span{width:12px;height:12px;border-radius:50%;border:2px solid var(--white)}
.dots span.on{background:var(--red)}
.widget{top:752px;width:303px;height:455px;border:1px solid var(--line);background:var(--white)}
.widget-head{height:52px;background:var(--purple);color:var(--white);font-family:'Raleway',sans-serif;font-size:19px;text-align:center;line-height:52px}
.listing{display:flex;gap:12px;padding:22px 10px 0 11px;height:133px;border-bottom:1px solid var(--line)}
.listing:last-child{border-bottom:none}
.thumb{flex:none;width:95px;height:78px;margin-top:2px}
.listing h4{font-family:'Raleway',sans-serif;font-weight:500;font-size:15px;color:var(--red);margin-bottom:6px}
.listing p{font-family:'Raleway',sans-serif;font-size:13.5px;line-height:20px;color:#444}
.news{padding:22px 14px}
.news p{font-family:'Raleway',sans-serif;font-size:15px;line-height:27px;padding-left:5px}
.news label{display:block;font-family:'Raleway',sans-serif;font-size:15px;margin-top:12px}
.field{border:1px solid #cfcfcf;background:var(--white);height:42px}
.news .field{margin-top:12px}
.btn{display:inline-block;font-family:'Raleway',sans-serif;font-size:16px;color:var(--white);background:var(--red);border-radius:3px;height:42px;line-height:42px;text-align:center}
.news .btn{width:152px;margin-top:18px}
.join{margin:18px 0 0 5px;width:261px;height:132px;padding:4px;border:1px solid #bbb;position:relative;background:linear-gradient(180deg,#8fa6b8,#5a5440 55%,#6b7c4d)}
.join span{position:absolute;right:30px;bottom:18px;color:var(--white);font-family:'Raleway',sans-serif;font-size:16px}
.proposal{padding:22px 13px}
.proposal .field{height:40px;margin-bottom:11px;font-family:'Raleway',sans-serif;font-size:15px;color:#333;padding:10px 12px}
.proposal .field.msg{height:70px}
.proposal .field sup{color:var(--red);font-size:10px}
.captcha{display:flex;align-items:center;gap:18px;margin:3px 0 0 8px;font-family:'Roboto',sans-serif;font-size:19px;letter-spacing:2px}
.captcha i{width:26px;height:26px;border-radius:50%;border:3px solid #e06030;display:block}
.proposal .btns{display:flex;gap:10px;margin-top:14px;padding-left:2px}
.proposal .btn{width:112px}
.proposal .btn.alt{background:var(--purple);width:112px}
.upcoming{left:0;top:1241px;width:1200px;height:494px;background:var(--grey-bg)}
.up-title{left:0;top:1270px;width:1200px;text-align:center;font-family:'Raleway',sans-serif;font-size:25px;color:#222}
.up-title b{color:var(--red);font-weight:700}
.up-text{left:200px;top:1316px;width:800px;text-align:center;font-size:15px;line-height:26px;color:#444;font-weight:300}
.card-side{top:1457px;width:189px;height:150px}
.card-main{left:427px;top:1398px;width:337px;height:302px;border:1px solid #ccc;background:var(--white)}
.card-main .pic{position:absolute;left:46px;top:31px;width:244px;height:190px;background:linear-gradient(180deg,#c0822e,#e3a03f 40%,#3b3a3a 55%,#b57a2a 75%,#5a3b1d)}
.tag{background:#1e1e1e;color:var(--white);font-family:'Roboto',sans-serif;font-weight:500;text-align:center}
.tag.sm{font-size:12px;height:35px;line-height:35px;width:222px}
.tag.lg{position:absolute;left:27px;top:220px;width:281px;height:48px;line-height:48px;font-size:16px}
.arrow{top:1535px;width:30px;height:30px;border-radius:50%;background:#1e1e1e}
.footer{left:0;top:1735px;width:1200px;height:420px;background:var(--purple)}
.fcol{top:1795px;color:var(--white)}
.fcol h5{font-family:'Raleway',sans-serif;font-weight:600;font-size:19px;margin-bottom:28px}
.fcol ul{list-style:none}
.quick li{font-family:'Raleway',sans-serif;font-size:16px;line-height:28px}
.posts li{display:flex;gap:12px;font-family:'Raleway',sans-serif;font-size:15px;line-height:25px;margin-bottom:11px}
.posts li b{font-weight:400;font-size:13px;flex:none}
.social{display:flex;gap:20px;margin-bottom:18px}
.social span{width:34px;height:34px;border-radius:50%;border:2px solid var(--white)}
.finfo li{display:flex;gap:22px;font-family:'Raleway',sans-serif;font-size:16px;line-height:25px;margin-bottom:13px}
.finfo svg{flex:none;margin-top:5px}
.bottombar{left:0;top:2155px;width:1200px;height:73px;background:var(--red)}
.copy{left:108px;top:2180px;font-family:'Raleway',sans-serif;font-size:15px;color:var(--white)}
.fbrand{left:541px;top:2096px;width:118px;height:118px;border-radius:50%;background:var(--purple);border:5px solid var(--white);display:flex;align-items:center;justify-content:center;text-align:center;font-family:'Raleway',sans-serif;font-weight:700;font-size:15px;line-height:1.15;color:var(--white)}
.badge{top:2170px;width:36px;height:40px;background:var(--white)}
</style>
</head>
<body>
<div class="abs topline"></div>

<header>
  <div class="abs brand"><span class="brand-dot"></span><span class="brand-name">The Coastal Bidding Firm</span></div>
  <div class="abs contact-addr">
    <svg width="18" height="20" viewBox="0 0 18 20"><path d="M9 1a6 6 0 0 0-6 6c0 4.5 6 10 6 10s6-5.5 6-10a6 6 0 0 0-6-6zm0 8.5A2.5 2.5 0 1 1 9 4.5a2.5 2.5 0 0 1 0 5z" fill="#c8163a"/><rect x="3" y="18" width="12" height="2" fill="#c8163a"/></svg>
    <div>THE COASTAL BIDDING FIRM<br>GROUP<br>P.O. Box 682<br>Gadsden, AL 35917</div>
  </div>
  <div class="abs contact-lines">
    <div class="row"><svg width="14" height="14" viewBox="0 0 14 14"><path d="M3 1l2 3-1.5 1.5a8 8 0 0 0 5 5L10 9l3 2-1.5 2.5C6 13 1 8 .5 2.5z" fill="#c8163a"/></svg><span>PHONE: (800)519-6084 or<br>(256)583-9101</span></div>
    <div class="row"><svg width="14" height="14" viewBox="0 0 14 14"><rect x="0" y="4" width="14" height="9" rx="1" fill="#c8163a"/><rect x="3" y="0" width="8" height="5" fill="#c8163a"/><rect x="3" y="7" width="8" height="1.5" fill="#fff"/></svg><span>FAX: (256)583-2260</span></div>
    <div class="row"><svg width="14" height="12" viewBox="0 0 14 12"><rect x=".8" y=".8" width="12.4" height="10" fill="none" stroke="#c8163a" stroke-width="1.6"/><path d="M1 1l6 5 6-5" fill="none" stroke="#c8163a" stroke-width="1.6"/></svg><span>EMAIL: info@coastal-bidding.example</span></div>
  </div>
</header>

<svg class="abs deco" viewBox="0 0 1200 470" aria-hidden="true"><polygon points="0,80 107,20 107,380 0,420" fill="#f1f1f3"/><polygon points="1093,60 1200,0 1200,300 1093,360" fill="#f1f1f3"/></svg>

<nav class="abs nav">
  <ul>
    <li class="active">Home</li><li>Auction Calendar</li><li>Auction Results</li><li>For Sale</li><li>Services</li><li>About Us</li><li>Contact Us</li>
  </ul>
</nav>

<section class="abs slider"><div class="slide" role="img" aria-label="Real estate photo: red waterfront cabins on a rocky coastline under a blue sky"></div></section>
<div class="abs slide-title">Coastal Bidding Company</div>
<div class="abs dots"><span></span><span class="on"></span><span></span></div>

<ul class="abs dropdown"><li>&gt;&gt; Live Auctions</li><li>&gt;&gt; Online Auctions</li></ul>

<section class="abs widget" style="left:107px">
  <div class="widget-head">FEATURED LISTINGS</div>
  <div class="listing"><div class="thumb" role="img" aria-label="Waterfront estate house on green lawn" style="background:linear-gradient(#9bb8d4,#5f7f45 55%,#6e9a3a)"></div><div><h4>140+/- Acres</h4><p>140+/- waterfront acres located on Neely Henry Lake.</p></div></div>
  <div class="listing"><div class="thumb" role="img" aria-label="Log cabin ranch home" style="background:linear-gradient(#a8c0d8,#8a5a32 50%,#6f8a3e)"></div><div><h4>Ideal Recreational Retreat</h4><p>487+/- Acre cattle ranch in Madison, GA. Ideal recrea tional retreat!</p></div></div>
  <div class="listing"><div class="thumb" role="img" aria-label="White house with blue sky and lawn" style="background:linear-gradient(#3f7fc8,#c9d3dd 50%,#5f8d3a)"></div><div><h4>ABSOLUTE AUCTION</h4><p>48+/- acres with 210,000+/- sq.ft. of ware house and office space.</p></div></div>
</section>

<section class="abs widget news-w" style="left:449px">
  <div class="widget-head">JOIN OUR NEWSLETTER</div>
  <div class="news">
    <p>Sign Up to receive our FREE Auction Alerts!</p>
    <label>Email Address:</label>
    <div class="field"></div>
    <span class="btn">Submit Now</span>
    <div class="join" role="img" aria-label="Stone manor house at dusk"><span>Join Us Now!</span></div>
  </div>
</section>

<section class="abs widget" style="left:789px">
  <div class="widget-head">REQUEST A PROPOSAL</div>
  <div class="proposal">
    <div class="field">Full Name<sup>*</sup></div>
    <div class="field">Email<sup>*</sup></div>
    <div class="field">Phone<sup>*</sup></div>
    <div class="field msg">Message</div>
    <div class="field">Type the text</div>
    <div class="captcha"><span>W6 8HP</span><i></i></div>
    <div class="btns"><span class="btn">Submit</span><span class="btn alt">Reset</span></div>
  </div>
</section>

<section class="abs upcoming"></section>
<h2 class="abs up-title">UPCOMING <b>AUCTIONS</b></h2>
<p class="abs up-text">The Coastal Bidding Firm, Inc. is a real estate auction company that specializes in combining cutting edge marketing practices with exciting auction events.</p>
<span class="abs arrow" style="left:40px"><svg width="30" height="30" viewBox="0 0 30 30"><path d="M17 9l-6 6 6 6" stroke="#fff" stroke-width="3" fill="none"/></svg></span>
<span class="abs arrow" style="left:1125px"><svg width="30" height="30" viewBox="0 0 30 30"><path d="M13 9l6 6-6 6" stroke="#fff" stroke-width="3" fill="none"/></svg></span>
<div class="abs card-side" style="left:163px" role="img" aria-label="Luxury home with swimming pool and lounge chairs"><div style="height:150px;background:linear-gradient(#6f9bc8,#7a7060 45%,#4aa0c8 75%,#3a3a3a)"></div></div>
<div class="abs tag sm" style="left:146px;top:1607px">Began: 11/12/15 at 3:00 PM CST</div>
<div class="abs card-main"><div class="pic" role="img" aria-label="Sunset over a lake with a small boat"></div><div class="tag lg">Began: 01/16/16 at 11:00 AM CST</div></div>
<div class="abs card-side" style="left:839px" role="img" aria-label="Aerial view of a large warehouse and parking lot"><div style="height:150px;background:linear-gradient(#5f8fcf,#6d8a55 30%,#8a9a7a 65%,#5d7a45)"></div></div>
<div class="abs tag sm" style="left:823px;top:1607px">Began: 12/08/15 at 1:00 PM EST</div>

<footer class="abs footer"></footer>
<div class="abs fcol" style="left:107px">
  <h5>QUICK LINKS</h5>
  <ul class="quick"><li>Home</li><li>Auction Calendar</li><li>Auction Results</li><li>For Sale</li><li>Services</li><li>About Us</li><li>Contact Us</li></ul>
</div>
<div class="abs fcol" style="left:314px;width:240px">
  <h5>NEWS &amp; EVENTS BLOG</h5>
  <ul class="posts"><li><b>&gt;&gt;</b>The increase in visibility of the auction industry</li><li><b>&gt;&gt;</b>This commitment to excel lence is the reason</li><li><b>&gt;&gt;</b>This creates a competitive auction atmosphere</li></ul>
</div>
<div class="abs fcol" style="left:608px;width:230px">
  <h5>CONTACT INFO</h5>
  <div class="social"><span></span><span></span><span></span><span></span></div>
  <ul class="finfo">
    <li><svg width="12" height="16" viewBox="0 0 12 16"><path d="M6 0a5 5 0 0 0-5 5c0 4 5 10 5 10s5-6 5-10a5 5 0 0 0-5-5zm0 7a2 2 0 1 1 0-4 2 2 0 0 1 0 4z" fill="#fff"/></svg><span>P.O. Box 682 Gadsden, AL 35917</span></li>
    <li><svg width="12" height="12" viewBox="0 0 14 14"><path d="M3 1l2 3-1.5 1.5a8 8 0 0 0 5 5L10 9l3 2-1.5 2.5C6 13 1 8 .5 2.5z" fill="#fff"/></svg><span>(800)519-6084</span></li>
    <li><svg width="13" height="11" viewBox="0 0 14 12"><rect x=".8" y=".8" width="12.4" height="10" fill="none" stroke="#fff" stroke-width="1.6"/><path d="M1 1l6 5 6-5" fill="none" stroke="#fff" stroke-width="1.6"/></svg><span>E-mail: info@coastal-<br>bidding.example</span></li>
  </ul>
</div>
<div class="abs fcol" style="left:892px;width:210px">
  <h5>FEATURED AUCTIONS</h5>
  <ul class="posts"><li><b>&gt;&gt;</b>The increase in visibility of the auction industry</li><li><b>&gt;&gt;</b>This commitment to excel lence is the reason</li><li><b>&gt;&gt;</b>This creates a competitive auction atmosphere</li></ul>
</div>

<div class="abs bottombar"></div>
<div class="abs copy">© 2016. The Coastal Bidding Firm. All Rights Reserved</div>
<div class="abs fbrand">The Coastal<br>Bidding<br>Firm</div>
<span class="abs badge" style="left:992px"></span>
<span class="abs badge" style="left:1046px"></span>
</body>
</html>
```